Corvane Holdings , new business card design

investment firm with corporate clients . need double sided business card , vertical and horizontal options ,logo must be clear. prefer pantone colors only and sharp design. website also www.corvane.ae

Khalid Bin Tarrafi
Managing Director
Tel. +971 4 387 2940
Mobile +971 50 518 2403
khalid@corvane.ae
Q-Span Plaza, officw 18-B07, Warqa Gardens, Dubai

Contact Information for Business Card

Khalid Bin Tarrafi
Managing Director

Font styles to use
Serif

Colors

Designer to choose colors to be used in the design.

```html
<!DOCTYPE html>
<html lang="en">
<head>
<meta charset="utf-8">
<title>Corvane Holdings – Business Card</title>
<link href="https://fonts.googleapis.com/css2?family=Lato:wght@300;400&display=swap" rel="stylesheet">
<style>
  :root {
    --page: #e7e5e2;
    --card-black: #0b0b0d;
    --card-white: #f6f6f7;
    --brand-blue: #41698f;
    --ink: #2b2b2d;
    --ink-soft: #4a4a4d;
    --rule: #5a5a5c;
    --white: #ffffff;
  }
  * { box-sizing: border-box; margin: 0; padding: 0; }
  html, body {
    width: 1200px; height: 1200px; overflow: hidden;
    background: var(--page);
    font-family: "Lato", Arial, sans-serif;
  }
  .card {
    position: absolute; left: 150px;
    width: 900px; height: 514px;
    overflow: hidden;
    box-shadow: 0 10px 30px rgba(0,0,0,0.18);
  }
  /* Logo side */
  .card--logo { top: 60px; background: var(--card-black); }
  .brand-mark {
    position: absolute; top: 50%; left: 50%;
    transform: translate(-50%, -50%);
    display: flex; align-items: center; gap: 22px;
    color: var(--white);
    font-weight: 300; font-size: 46px;
    letter-spacing: 14px; text-transform: uppercase;
    white-space: nowrap;
  }
  .brand-mark__square { width: 22px; height: 22px; background: var(--white); }

  /* Contact side */
  .card--contact { top: 626px; background: var(--card-white); color: var(--ink); }
  .card__wave { position: absolute; inset: 0; width: 100%; height: 100%; }
  .person { position: absolute; left: 70px; top: 58px; }
  .person__name { font-size: 38px; font-weight: 400; }
  .person__title { font-size: 22px; color: var(--ink-soft); margin-top: 2px; }
  .rule { position: absolute; left: 70px; width: 500px; height: 2px; background: var(--rule); }
  .rule--top { top: 150px; }
  .rule--bottom { top: 318px; }
  .contact-list { position: absolute; left: 70px; top: 170px; font-size: 28px; line-height: 44px; }
  .contact-list__row { display: flex; }
  .contact-list__label { width: 120px; }
  .address { position: absolute; left: 70px; top: 340px; font-size: 19px; line-height: 28px; color: var(--ink-soft); }
  .side-brand {
    position: absolute; right: 36px; top: 70px;
    writing-mode: vertical-rl;
    color: var(--white); font-weight: 300; font-size: 24px;
    letter-spacing: 7px; text-transform: uppercase; white-space: nowrap;
  }
  .side-web {
    position: absolute; right: 96px; top: 110px;
    writing-mode: vertical-rl;
    color: var(--white); font-size: 18px; letter-spacing: 1px; white-space: nowrap;
  }
</style>
</head>
<body>
  <section class="card card--logo">
    <div class="brand-mark">
      <span class="brand-mark__square"></span>
      <span class="brand-mark__name">Corvane Holdings</span>
    </div>
  </section>

  <section class="card card--contact">
    <svg class="card__wave" viewBox="0 0 900 514" preserveAspectRatio="none" aria-hidden="true">
      <path d="M300 514 C540 480 700 330 730 0 L900 0 L900 514 Z" fill="var(--brand-blue)"/>
    </svg>

    <div class="person">
      <div class="person__name">Khalid Bin Tarrafi</div>
      <div class="person__title">Managing Director</div>
    </div>
    <div class="rule rule--top"></div>

    <div class="contact-list">
      <div class="contact-list__row"><span class="contact-list__label">Tel</span><span>: +971 4 387 2940</span></div>
      <div class="contact-list__row"><span class="contact-list__label">Mobile</span><span>: +971 50 518 2403</span></div>
      <div class="contact-list__row"><span class="contact-list__label">Email</span><span>: khalid@corvane.ae</span></div>
    </div>
    <div class="rule rule--bottom"></div>

    <div class="address">Q-Span Plaza, officw 18-B07,<br>Warqa Gardens, Dubai</div>

    <div class="side-brand">Corvane Holdings</div>
    <div class="side-web">www.corvane.ae</div>
  </section>
</body>
</html>
```